Inspirational Quotes Poster Set

Brookloft is a stylish coworking space, which has a design-oriented vintage look from the 60's with an industrial touch (www.brookloft-example.com) Brookloft Quote Poster Set of 16 posters. The poster should be typo oriented and rather simple. Reflecting a bit the clean billboard design from the sixties. Minimal / simple graphical elements

Target Market(s)

Startups and Entrepreneurs

Industry/Entity Type

Startup

Font styles to use
Sans Serif

Colors

Designer to choose colors to be used in the design.

Requirements
Must have
• Posters need to be on and very stylish

```html
<!DOCTYPE html>
<html lang="en">
<head>
<meta charset="utf-8">
<title>Brookloft Quote Poster Set – Keep Going</title>
<link rel="stylesheet" href="https://fonts.googleapis.com/css2?family=Libre+Franklin:wght@600;700;800&display=swap">
<style>
  :root {
    --poster-red: #be1622;
    --paper-white: #ffffff;
  }
  html, body {
    margin: 0;
    padding: 0;
    width: 801px;
    height: 1200px;
    overflow: hidden;
    background: var(--paper-white);
  }
  .poster {
    display: block;
    width: 801px;
    height: 1200px;
    font-family: "Libre Franklin", Arial, sans-serif;
  }
  .poster__band { fill: var(--poster-red); }
  .quote-lead {
    fill: var(--poster-red);
    font-weight: 700;
    font-size: 50px;
  }
  .quote-lead--knockout { fill: var(--paper-white); }
  .quote-headline {
    fill: var(--paper-white);
    font-weight: 700;
    font-size: 330px;
  }
  .attribution {
    fill: var(--paper-white);
    font-weight: 800;
    font-size: 22px;
    letter-spacing: 1px;
  }
  .brand-name {
    fill: var(--paper-white);
    font-weight: 800;
    font-size: 38px;
  }
</style>
</head>
<body>
<svg class="poster" viewBox="0 0 801 1200" xmlns="http://www.w3.org/2000/svg">
  <defs>
    <clipPath id="above-band"><rect x="0" y="0" width="801" height="262"/></clipPath>
    <clipPath id="inside-band"><rect x="0" y="262" width="801" height="938"/></clipPath>
  </defs>

  <rect class="poster__band" x="0" y="262" width="801" height="938"/>

  <g class="quote-lead-group">
    <text class="quote-lead" x="35" y="254" textLength="735" lengthAdjust="spacingAndGlyphs" clip-path="url(#above-band)">if you’re going through hell,</text>
    <text class="quote-lead quote-lead--knockout" x="35" y="254" textLength="735" lengthAdjust="spacingAndGlyphs" clip-path="url(#inside-band)">if you’re going through hell,</text>
  </g>

  <text class="quote-headline" x="32" y="492" textLength="746" lengthAdjust="spacingAndGlyphs">keep</text>
  <text class="quote-headline" x="-22" y="783" textLength="845" lengthAdjust="spacingAndGlyphs">going</text>

  <text class="attribution" x="70" y="1039" textLength="227" lengthAdjust="spacingAndGlyphs">Edwin Marlowe,</text>
  <text class="attribution" x="71" y="1067" textLength="274" lengthAdjust="spacingAndGlyphs">Writer and Statesman</text>

  <text class="brand-name" x="400" y="1143" text-anchor="middle">Brookloft</text>
</svg>
</body>
</html>
```